swimming pool Leak Detection Brochure

I would Like to create a pool leak detection brochure

Target Market(s)

High end Clients with inground swimming pools

Industry/Entity Type

Pool Service

Font styles to use
Other font styles liked:
• Im open to suggestions but using my website for ideas is suggested

Colors

Designer to choose colors to be used in the design.

Requirements
Must have
• Do you Have a Leak??
• Figuring out when your pool has a leak can be tough. Environmental factors do play a role in the water level, and just because your pool’s water is lower than normal does not mean it has a leak. Wind, humidity, and sun exposure all impact your rate of evaporation.
• Warning Signs of a Leak in Your Pool
• Your pool, fountain, or spa loses more than 1/4 an inch of water a day
• There are cracks in or around the pool decking
• You need to add water more than once a week
• Grass around the area is soggy
• Your pool deck is sinking or lifting
Nice to have
• PREPARING FOR A LEAK TEST
• To ensure you receive an accurate leak detection test, it is required that you have the pool vacuumed and cleaned beforehand. Dirt and debris in the pool can make it difficult to spot even large leaks. Likewise, the water should be as clear as possible. If your water is green it means mildew, algae, or fungi has infested it. Not only does this make it impossible to test for leaks, but it’s dangerous for our health. Finally our pool should be full to the normal level - we can’t find a leak that is not leaking! After your test, you will be confident knowing you have a pool/fountain/spa that is free of leaks or the Leak has been found and can be repaired Properly.

```html
<!DOCTYPE html>
<html lang="en">
<head>
<meta charset="utf-8">
<title>Harbor Pool Service – Leak Detection Brochure Cover</title>
<link rel="stylesheet" href="https://fonts.googleapis.com/css2?family=Sorts+Mill+Goudy&family=Open+Sans:wght@400;700&display=swap">
<style>
  :root {
    --backdrop: #e4e6ea;
    --navy: #1d3f86;
    --royal: #2d5fb4;
    --mid-blue: #3a74c4;
    --sky-blue: #5b94d6;
    --pale-line: #8fc0ee;
    --orange: #e0662a;
    --white: #ffffff;
    --photo-sky: #6fa3dc;
    --photo-green: #4f8a4a;
    --photo-pool: #1f63d0;
  }
  * { margin: 0; padding: 0; box-sizing: border-box; }
  html, body {
    width: 1200px;
    height: 789px;
    overflow: hidden;
    background: var(--backdrop);
  }
  .canvas {
    position: relative;
    width: 1200px;
    height: 789px;
    display: flex;
    align-items: center;
    justify-content: center;
  }
  .brochure-cover {
    position: relative;
    width: 524px;
    height: 741px;
    box-shadow: 0 6px 24px rgba(0, 0, 0, 0.18);
    overflow: hidden;
    background: var(--royal);
  }
  .cover-art { position: absolute; inset: 0; display: block; }
  .brand-badge {
    position: absolute;
    left: 298px;
    top: 336px;
    width: 160px;
    height: 160px;
    border-radius: 50%;
    background: var(--white);
    border: 4px solid var(--orange);
    display: flex;
    align-items: center;
    justify-content: center;
    text-align: center;
  }
  .brand-name {
    font-family: "Open Sans", sans-serif;
    font-weight: 700;
    font-size: 19px;
    line-height: 1.15;
    color: var(--navy);
    letter-spacing: 0.5px;
  }
  .cover-headline {
    position: absolute;
    left: 80px;
    top: 582px;
    font-family: "Sorts Mill Goudy", serif;
    font-size: 29px;
    line-height: 1.22;
    color: var(--white);
  }
  .cover-url {
    position: absolute;
    right: 20px;
    top: 650px;
    font-family: "Open Sans", sans-serif;
    font-size: 14px;
    color: var(--white);
    padding-bottom: 6px;
    border-bottom: 2px solid var(--orange);
  }
  .cover-url strong { font-weight: 700; }
</style>
</head>
<body>
<main class="canvas">
  <article class="brochure-cover">
    <svg class="cover-art" viewBox="0 0 524 741" width="524" height="741" aria-hidden="false">
      <defs>
        <linearGradient id="photoTones" x1="0" y1="0" x2="0" y2="1">
          <stop offset="0" stop-color="var(--photo-sky)"/>
          <stop offset="0.22" stop-color="#8fb8e4"/>
          <stop offset="0.3" stop-color="var(--photo-green)"/>
          <stop offset="0.42" stop-color="#3d7fd8"/>
          <stop offset="1" stop-color="var(--photo-pool)"/>
        </linearGradient>
        <linearGradient id="lowerBand" x1="0" y1="0" x2="1" y2="1">
          <stop offset="0" stop-color="var(--sky-blue)"/>
          <stop offset="1" stop-color="var(--royal)"/>
        </linearGradient>
      </defs>
      <rect class="lower-band" x="0" y="0" width="524" height="741" fill="url(#lowerBand)"/>
      <path class="wave-dark" d="M0 420 C 150 520, 360 540, 524 410 V 520 C 380 600, 170 590, 0 500 Z" fill="var(--navy)" opacity="0.55"/>
      <path class="wave-mid" d="M0 440 C 160 540, 370 545, 524 420 V 470 C 380 570, 160 570, 0 480 Z" fill="var(--mid-blue)"/>
      <path class="pool-photo" role="img" aria-label="Photo of a resort swimming pool with palm trees, a modern building and swimmers in bright blue water"
            d="M0 0 H524 V390 C 430 480, 240 520, 0 440 Z" fill="url(#photoTones)"/>
      <path class="accent-line" d="M0 446 C 160 540, 370 548, 524 416" fill="none" stroke="var(--pale-line)" stroke-width="1"/>
    </svg>
    <div class="brand-badge">
      <span class="brand-name">Harbor<br>Pool Service</span>
    </div>
    <h1 class="cover-headline">Dive Into<br>Professional Pool<br>Service &amp; Repair</h1>
    <p class="cover-url">www.<strong>harborpoolco</strong>.com</p>
  </article>
</main>
</body>
</html>
```